Business Card Design

We need a design for business cards for our company. We have a logo. We teach EMT's and we are based out of Virginia. The information that will need to add would be, name, title, phone number, email, address. On the back of the business card would be "We help you, help others"

Target Market(s)

People that want to become EMT's

Colors

Designer to choose colors to be used in the design.

Requirements
Must have
• company logo

```html
<!DOCTYPE html>
<html lang="en">
<head>
<meta charset="utf-8">
<title>Rescue Path Academy – Business Card</title>
<link rel="stylesheet" href="https://fonts.googleapis.com/css2?family=Montserrat:wght@500;600&family=Work+Sans:wght@400;500&display=swap">
<style>
  :root {
    --brand-red: #be1e2d;
    --ink-grey: #7a7a7a;
    --soft-grey: #9a9a9a;
    --card-white: #ffffff;
    --tint-red: #f7e6e8;
    --backdrop: #d4d4d4;
  }
  * { box-sizing: border-box; margin: 0; padding: 0; }
  html, body { width: 1200px; height: 930px; overflow: hidden; }
  body {
    background: var(--backdrop);
    font-family: "Work Sans", sans-serif;
    position: relative;
  }
  .card {
    position: absolute;
    width: 560px;
    height: 320px;
    border-radius: 22px;
    overflow: hidden;
    box-shadow: 0 6px 18px rgba(0,0,0,0.18);
  }
  .card--back {
    left: 90px; top: 110px;
    background: var(--brand-red);
    display: flex; align-items: center; justify-content: center;
  }
  .card--front {
    left: 560px; top: 500px;
    background: var(--card-white);
  }
  .brand-name {
    font-family: "Montserrat", sans-serif;
    font-weight: 600;
    letter-spacing: 0.04em;
    display: flex; align-items: center; gap: 10px;
  }
  .card--back .brand-name { color: var(--card-white); font-size: 30px; }
  .card--back .brand-dot { width: 16px; height: 16px; border-radius: 50%; background: var(--card-white); }
  .card--front .brand-name {
    position: absolute; right: 34px; top: 34px;
    color: var(--brand-red); font-size: 20px;
  }
  .card--front .brand-dot { width: 11px; height: 11px; border-radius: 50%; background: var(--brand-red); }
  .backdrop-motif {
    position: absolute; left: 70px; top: 105px;
    width: 300px; height: 215px;
    background: linear-gradient(180deg, var(--tint-red), #f6f3f3);
    opacity: 0.8;
  }
  .divider-long {
    position: absolute; left: 150px; right: 30px; top: 150px;
    height: 1.5px; background: var(--brand-red);
  }
  .person {
    position: absolute; left: 0; top: 172px;
    padding-left: 26px;
    border-left: 10px solid var(--brand-red);
  }
  .person-name {
    font-family: "Montserrat", sans-serif;
    font-weight: 600; font-size: 23px;
    color: var(--brand-red); letter-spacing: 0.02em;
  }
  .person-title { font-size: 15px; color: var(--soft-grey); margin-top: 2px; }
  .divider-short {
    position: absolute; left: 36px; top: 232px;
    width: 200px; height: 1.5px; background: var(--brand-red);
  }
  .contact {
    position: absolute; left: 40px; top: 244px;
    list-style: none; font-size: 15px; color: var(--ink-grey);
    line-height: 22px;
  }
  .contact li { display: flex; align-items: center; gap: 10px; }
  .contact svg { width: 12px; height: 12px; flex: none; }
  .contact .accent { color: var(--brand-red); }
  .address {
    position: absolute; right: 34px; top: 168px;
    text-align: right; font-size: 15px; line-height: 22px;
    color: var(--ink-grey);
  }
</style>
</head>
<body>
  <section class="card card--back">
    <div class="brand-name"><span class="brand-dot"></span>RESCUE PATH ACADEMY</div>
  </section>

  <section class="card card--front">
    <div class="backdrop-motif" role="img" aria-label="Faint medical decoration with heartbeat line"></div>
    <div class="brand-name"><span class="brand-dot"></span>RESCUE PATH ACADEMY</div>
    <div class="divider-long"></div>
    <div class="person">
      <p class="person-name">DANIEL HART</p>
      <p class="person-title">Director</p>
    </div>
    <div class="divider-short"></div>
    <ul class="contact">
      <li>
        <svg viewBox="0 0 12 12"><path d="M2.5 1l2 2.3-1 1.2a7 7 0 0 0 4 4l1.2-1 2.3 2-1.3 1.5C5.5 10.8 1.2 6.5 1 2.3z" fill="#be1e2d"/></svg>
        555-201-4470
      </li>
      <li>
        <svg viewBox="0 0 12 12"><rect x="1" y="2.5" width="10" height="7" fill="none" stroke="#be1e2d" stroke-width="1.3"/><path d="M1 3l5 3.5L11 3" fill="none" stroke="#be1e2d" stroke-width="1.3"/></svg>
        info@rescuepath.com
      </li>
      <li>
        <svg viewBox="0 0 12 12"><circle cx="6" cy="6" r="5" fill="none" stroke="#be1e2d" stroke-width="1.3"/><path d="M1 6h10M6 1c-2.5 2.8-2.5 7.2 0 10M6 1c2.5 2.8 2.5 7.2 0 10" fill="none" stroke="#be1e2d" stroke-width="1"/></svg>
        <span>www.<span class="accent">rescuepath</span>.com</span>
      </li>
    </ul>
    <address class="address" style="font-style:normal">
      410 Linden Ave.<br>
      Fairview, VA 22000
    </address>
  </section>
</body>
</html>
```